Help our Sugar Loom find our winning design! We're looking for a business card....

We’re a Sugar Loom in NY specializing in custom-made cakes and unique desserts.
Our cakes combine flavor and art, each designed to match customer’s special event and theme.
We’d like a unique business card with a clean design that will combine French chic and artistic look & feel.
We’d like to differentiate ourselves from standard bakeries, please don’t offer cupcake images :-)
Our logo is peach-pink and brown and we’d love to use these colors ( . Another color that can be added is gold - or feel free to suggest!

Target Market(s)

Women, ages 25-55

Industry/Entity Type

Boutique

Contact Information for Business Card

Text on card:
Logo
Sugar Loom by Dana Welch

www.sugarloomsweets.com
hello@sugarloom.com
(516) 555-0147
F – sugarloomnyc
IG - sugarloom_ny

Font styles to use
Sans Serif
Script

Requirements
Must have
• Logo
• Clean look
• French chic and artistic look & feel.
Nice to have
• Damask pattern
Should not have
• Cupcake images

```html
<!DOCTYPE html>
<html lang="en">
<head>
<meta charset="utf-8">
<title>Sugar Loom – Business Card</title>
<link rel="stylesheet" href="https://fonts.googleapis.com/css2?family=Great+Vibes&family=Lato:wght@400;700&family=EB+Garamond:wght@400&display=swap">
<style>
  :root {
    --backdrop: #a9a9a9;
    --cocoa: #2a1a1c;
    --cocoa-deep: #1f1315;
    --peach: #dba79c;
    --peach-soft: #f3ddd7;
    --ink: #2b2224;
    --paper: #ffffff;
  }
  * { box-sizing: border-box; margin: 0; padding: 0; }
  html, body {
    width: 1200px; height: 852px; overflow: hidden;
    background: var(--backdrop);
  }
  .canvas { position: relative; width: 1200px; height: 852px; }

  .card {
    position: absolute; width: 500px; height: 286px;
    border-radius: 22px; overflow: hidden;
    box-shadow: 0 6px 16px rgba(0,0,0,0.25);
  }

  /* front */
  .card-front { left: 90px; top: 140px; background: var(--cocoa); }
  .card-front .flourish {
    position: absolute; left: 70px; top: 48px; width: 360px; height: 190px;
    border-radius: 50%;
    background: radial-gradient(ellipse at center, rgba(219,167,156,0.22), rgba(219,167,156,0) 70%);
  }
  .card-front .brand-name {
    position: absolute; left: 0; right: 0; top: 112px; text-align: center;
    font-family: "Great Vibes", cursive; font-size: 50px; color: var(--peach);
  }

  /* back */
  .card-back { left: 610px; top: 430px; background: var(--paper); }
  .card-back .flourish {
    position: absolute; left: 18px; top: 70px; width: 250px; height: 140px;
    border-radius: 50%;
    background: radial-gradient(ellipse at center, rgba(219,167,156,0.28), rgba(219,167,156,0) 70%);
  }
  .card-back .brand-name {
    position: absolute; left: 18px; width: 250px; top: 112px; text-align: center;
    font-family: "Great Vibes", cursive; font-size: 38px; color: var(--ink);
  }
  .owner {
    position: absolute; right: 34px; top: 34px; text-align: center;
  }
  .owner-studio {
    font-family: "Lato", sans-serif; font-size: 15px; color: var(--ink);
  }
  .owner-name {
    font-family: "Great Vibes", cursive; font-size: 32px; color: var(--ink); line-height: 1.1;
  }
  .socials {
    position: absolute; right: 30px; top: 140px; list-style: none;
    font-family: "EB Garamond", serif; font-size: 15px; color: var(--ink);
  }
  .socials li { display: flex; align-items: center; gap: 8px; line-height: 20px; }
  .socials .mark {
    width: 10px; height: 10px; background: var(--ink); border-radius: 2px;
  }
  .contacts {
    position: absolute; left: 30px; top: 180px; list-style: none;
    font-family: "EB Garamond", serif; font-size: 16px; color: var(--ink);
  }
  .contacts li { display: flex; align-items: center; gap: 10px; line-height: 21px; }
  .contacts svg { width: 12px; height: 12px; fill: var(--ink); }
  .base-band { position: absolute; left: 0; bottom: 0; width: 500px; height: 20px; }
</style>
</head>
<body>
<main class="canvas">

  <section class="card card-front" aria-label="Card front">
    <div class="flourish" role="img" aria-label="Rose-gold swirl flourish ornament with tiered cake motif"></div>
    <div class="brand-name">Sugar Loom</div>
  </section>

  <section class="card card-back" aria-label="Card back">
    <div class="flourish" role="img" aria-label="Rose-gold swirl flourish ornament with tiered cake motif"></div>
    <div class="brand-name">Sugar Loom</div>

    <div class="owner">
      <p class="owner-studio">Sugar Loom by</p>
      <p class="owner-name">Dana Welch</p>
    </div>

    <ul class="socials">
      <li><span class="mark"></span>sugarloomnyc</li>
      <li><span class="mark"></span>sugarloom_ny</li>
    </ul>

    <ul class="contacts">
      <li>
        <svg viewBox="0 0 12 12" aria-hidden="true"><path d="M2 1h3l1 3-2 1c1 2 2 3 3 3l1-2 3 1v3c-5 1-10-4-9-9z"/></svg>
        (516) 555-0147
      </li>
      <li>
        <svg viewBox="0 0 12 12" aria-hidden="true"><path d="M1 3h10v7H1z M1 3l5 4 5-4" fill="none" stroke="#2b2224" stroke-width="1.2"/></svg>
        hello@sugarloom.com
      </li>
      <li>
        <svg viewBox="0 0 12 12" aria-hidden="true"><g fill="none" stroke="#2b2224" stroke-width="1"><circle cx="6" cy="6" r="5"/><ellipse cx="6" cy="6" rx="2.2" ry="5"/><path d="M1 6h10"/></g></svg>
        www.sugarloomsweets.com
      </li>
    </ul>

    <svg class="base-band" viewBox="0 0 500 20" preserveAspectRatio="none" aria-hidden="true">
      <polygon points="0,0 410,0 395,20 0,20" fill="var(--cocoa)"/>
      <polygon points="410,0 500,0 500,20 395,20" fill="var(--peach)"/>
    </svg>
  </section>

</main>
</body>
</html>
```